New Corporate Email Signature with Custom GIF KAV Electric LLC & KAV Fire & Security

Project Overview
KAV Electric LLC and KAV Fire & Security are seeking a professional, polished, and technically robust corporate email signature design. The project has two integrated deliverables:
A custom animated GIF representing both sides of our business
A complete corporate email signature layout designed for real-world compatibility (Gmail, Outlook, iOS, Android)
Our brand aesthetic is corporate, conservative, and clean. We value clarity, trust, professionalism, and subtle creativity β€” nothing overly flashy or cartoonish.
This design will be used across the entire company and must be visually aligned with our brand while remaining technically dependable.

PART 1 β€” Animated GIF Requirements
The GIF will be the core visual anchor of the new signature.
It must be clean, smooth, subtle, and optimized for email use.
βš™ Technical Requirements
Max file size: 150–200 KB (smaller is better)
Dimensions: approx 300px width (flexible, but must look good small)
Looping: continuous loop
Style: professional, minimalistic transitions

No rapid flashing or harsh animations
Must export cleanly into a format email clients accept

🎞 GIF Animation Sequence
Phase 1 β€” KAV Electric (KE)
Use the yellow β€œKE” avatar logo (provided).
Animation flow:
KE avatar appears
Full name β€œKAV Electric LLC” slides in, fades in, or otherwise appears smoothly
A scrolling or cycling list of service offerings displays:
EV Charging Stations
Generator & Transformers
Testing & Troubleshooting
LED Lighting Upgrades
After the list is shown, the entire KE segment fades out

Phase 2 β€” KAV Fire & Security (KF)
Use the red β€œKF” avatar logo (provided).
Animation flow mirrors Phase 1:
KF avatar appears
Full name β€œKAV Fire & Security” slides/fades in
Scrolling or cycling list of services displays:
Fire Alarm Upgrades
BQTL 48 Test & Inspect
Security Surveillance Systems
Access Control Systems
Data & Fiber Optic Cabling
Fade out β†’ loop back to KE
Creative Direction

Designers are encouraged to use:
Clean transitions
Soft fades
Professional typography
Modern minimalism
Consistent brand colors
High clarity at small sizes

Avoid:
Busy motion
Hard flashes
Excessive text overlays
Overly long transitions

The goal: a smooth, corporate-grade rotation that fits seamlessly into an email signature.

PART 2 β€” Corporate Email Signature Design

The signature must be visually appealing, brand-aligned, and structurally bulletproof across all major email systems.
πŸ“ Required Elements
πŸ‘€ Left Side Content
Circular headshot (we will supply final photos)
Social media icons with embedded URLs:
Facebook
LinkedIn
Google Business Profile
Instagram

Icons should be clean, modern, and in alignment with brand colors
πŸ“„ Right Side Content
Name
Title
KAV Electric LLC / KAV Fire & Security (depending on user)
Phone number
Email address
License# 52804
Physical office address: 384 Pembrook St, Westwood NJ 07912

Small CTA for newsletter signup (button or micro-banner)

🏒 Branding Assets Provided

You will receive:
KE avatar logo
KF avatar logo
Full-name KE logo
Full-name KF logo

These should be incorporated naturally and professionally.

Design Requirements

Conservative corporate styling

Clean typography

Balanced use of white space

Professional hierarchy

Light and dark mode compatibility preferred

Layout should not rely on one large image

All images should export cleanly for hosting on servers/CDN

Avoid overly tall signatures

The final signature must present as modern, trustworthy, and technically reliable across platforms.

πŸ§ͺ Compatibility Requirements

The signature must display correctly in:

Gmail (web and mobile)

Outlook (desktop & online)

Apple Mail

iPhone Mail

Android mail apps

Designers must avoid DIV-based layouts and instead propose a layout that can be implemented using table-based HTML, which is the industry standard for email compatibility.

You do not need to build the HTML β€” only supply the final layered design (PSD/AI/Figma) plus a clear structural layout that can be converted to HTML later.

πŸ“¦ Deliverables
1. Animated GIF

Final optimized GIF

Source file (After Effects, Photoshop, or equivalent)

Export guidelines so we can reproduce future versions

2. Email Signature Design

Full static design mockup

Modular layout for each employee

Icon set for social media

Newsletter CTA element

Clear spacing, alignment, and typography specifications

All source files (PSD, AI, Figma, etc.)

🧭 Creative Guidance Summary

We want:
βœ” Modern
βœ” Corporate
βœ” Minimalistic
βœ” Professional
βœ” Clean motion
βœ” Consistent branding
βœ” Email-safe elements

We do not want:
✘ Flashy marketing look
✘ Overly colorful or playful styles
✘ Hard-to-read fonts
✘ Heavy animation
✘ Oversized signatures

πŸ›  Tools & Format Flexibility

We allow full creative freedom regarding:

Animation style

Typography choices

Structuring of the two-column layout

How the service lists scroll or cycle

As long as the end result is clean, brand-aligned, professional, and email-compatible.

πŸ’¬ Final Note to Designers

We encourage creativity within the boundaries of corporate professionalism.
This signature will represent our company every time an email is sent β€” it must communicate trust, clarity, expertise, and brand strength.

```html
<!DOCTYPE html>
<html lang="en">
<head>
<meta charset="utf-8">
<title>KAV Fire &amp; Security – Email Signature</title>
<link href="https://fonts.googleapis.com/css2?family=Roboto:wght@400;700&display=swap" rel="stylesheet">
<style>
  :root {
    --brand-red: #e3202a;
    --brand-red-dark: #b8141c;
    --ink: #2f2f2f;
    --muted-grey: #6a6a6a;
    --ring-grey: #e6e6e6;
    --paper: #ffffff;
    --paper-tint: #f6f6f6;
    --rule: #dcdcdc;
  }
  * { margin: 0; padding: 0; box-sizing: border-box; }
  html, body {
    width: 1200px; height: 600px; overflow: hidden;
    background: var(--paper);
  }
  .signature {
    position: relative; width: 1200px; height: 600px; overflow: hidden;
    background: radial-gradient(circle at 30% 40%, var(--paper) 0%, var(--paper-tint) 100%);
    font-family: "Roboto", Arial, sans-serif;
    color: var(--ink);
  }
  .corner-band { position: absolute; }
  .corner-band--top { left: 0; top: 0; }
  .corner-band--bottom { right: 0; bottom: 0; }

  .headshot {
    position: absolute; left: 72px; top: 122px;
    width: 336px; height: 336px; border-radius: 50%;
    border: 12px solid var(--ring-grey);
    background: radial-gradient(circle at 50% 40%, #d9cbbd 0%, #b89a82 40%, #5d7f92 75%, #e9e9e9 100%);
    box-shadow: 0 6px 18px rgba(0,0,0,0.12);
  }

  .social-links {
    position: absolute; left: 93px; top: 477px;
    display: flex; gap: 27px; list-style: none;
  }
  .social-links__item {
    width: 54px; height: 54px; border-radius: 50%;
    background: var(--brand-red);
  }

  .brand-name {
    position: absolute; left: 519px; top: 28px;
    font-weight: 700; font-size: 40px; line-height: 1;
    color: var(--ink);
  }
  .brand-rule {
    position: absolute; left: 450px; top: 88px;
    width: 660px; height: 2px;
    background: linear-gradient(90deg, transparent, var(--rule) 30%, var(--rule) 80%, transparent);
  }

  .contact-list { position: absolute; left: 537px; top: 116px; list-style: none; }
  .contact-list__item {
    display: flex; align-items: center; height: 63px;
    font-size: 31px; line-height: 1;
  }
  .contact-list__icon { width: 30px; height: 30px; margin-right: 24px; flex: none; }
  .contact-list__icon svg { width: 30px; height: 30px; display: block; fill: var(--brand-red); }
  .contact-list__item--address { height: 126px; align-items: flex-start; }
  .contact-list__item--address .contact-list__icon { margin-top: 16px; }
  .contact-list__item--address .contact-list__text { line-height: 63px; }

  .newsletter-cta {
    position: absolute; left: 1029px; top: 120px;
    width: 120px; height: 426px; border-radius: 60px;
    background: var(--muted-grey);
    display: flex; align-items: center; justify-content: center;
  }
  .newsletter-cta__label {
    writing-mode: vertical-rl;
    color: var(--paper); font-weight: 700; font-size: 25px;
    letter-spacing: 2px; text-transform: uppercase; white-space: nowrap;
  }
</style>
</head>
<body>
<main class="signature">
  <svg class="corner-band corner-band--top" width="760" height="60" viewBox="0 0 760 60" aria-hidden="true">
    <path d="M0 0 H760 C600 10 400 20 0 50 Z" fill="var(--brand-red)"/>
    <path d="M0 50 C300 28 520 16 760 0 C520 22 300 40 0 60 Z" fill="var(--brand-red-dark)" opacity="0.35"/>
  </svg>

  <div class="headshot" role="img" aria-label="Circular portrait photo of the employee"></div>

  <ul class="social-links" aria-label="Social media profiles">
    <li class="social-links__item" aria-label="Social profile 1"></li>
    <li class="social-links__item" aria-label="Social profile 2"></li>
    <li class="social-links__item" aria-label="Social profile 3"></li>
    <li class="social-links__item" aria-label="Social profile 4"></li>
  </ul>

  <h1 class="brand-name">KAV Fire &amp; Security</h1>
  <div class="brand-rule"></div>

  <ul class="contact-list">
    <li class="contact-list__item">
      <span class="contact-list__icon"><svg viewBox="0 0 24 24"><circle cx="12" cy="7" r="5"/><path d="M2 23c0-6 4.5-9 10-9s10 3 10 9z"/></svg></span>
      <span class="contact-list__text">Daniel Rourke</span>
    </li>
    <li class="contact-list__item">
      <span class="contact-list__icon"><svg viewBox="0 0 24 24"><path d="M4 1h16v22h-6v-5h-4v5H4z M7 4v3h3V4z M14 4v3h3V4z M7 9v3h3V9z M14 9v3h3V9z M7 14v2h3v-2z M14 14v2h3v-2z" fill-rule="evenodd"/></svg></span>
      <span class="contact-list__text">Managing Director</span>
    </li>
    <li class="contact-list__item">
      <span class="contact-list__icon"><svg viewBox="0 0 24 24"><path d="M6.6 10.8a15.1 15.1 0 0 0 6.6 6.6l2.2-2.2a1 1 0 0 1 1-.25c1.1.37 2.3.57 3.6.57a1 1 0 0 1 1 1V20a1 1 0 0 1-1 1A17 17 0 0 1 3 4a1 1 0 0 1 1-1h3.5a1 1 0 0 1 1 1c0 1.25.2 2.45.57 3.57a1 1 0 0 1-.25 1z"/></svg></span>
      <span class="contact-list__text">+1 555 204 (7316)</span>
    </li>
    <li class="contact-list__item">
      <span class="contact-list__icon"><svg viewBox="0 0 24 24"><path d="M2 4h20v16H2z"/><path d="M3 5l9 7 9-7" fill="none" stroke="#fff" stroke-width="1.8"/></svg></span>
      <span class="contact-list__text">info@kavfiresecurity.com</span>
    </li>
    <li class="contact-list__item">
      <span class="contact-list__icon"><svg viewBox="0 0 24 24"><path d="M1 4h22v16H1z M3 7v2h18V7z M4 13v2h6v-2z M12 13v2h7v-2z" fill-rule="evenodd"/></svg></span>
      <span class="contact-list__text">License# 52804</span>
    </li>
    <li class="contact-list__item contact-list__item--address">
      <span class="contact-list__icon"><svg viewBox="0 0 24 24"><path d="M12 2 1 12h3v10h6v-6h4v6h6V12h3z"/></svg></span>
      <span class="contact-list__text">384 Pembrook St,<br>Lakeview NJ 07912</span>
    </li>
  </ul>

  <a class="newsletter-cta" aria-label="Join our newsletter">
    <span class="newsletter-cta__label">Join Our Newsletter</span>
  </a>

  <svg class="corner-band corner-band--bottom" width="360" height="60" viewBox="0 0 360 60" aria-hidden="true">
    <path d="M0 60 C140 50 260 30 360 0 V60 Z" fill="var(--brand-red)"/>
    <path d="M40 52 C170 38 270 20 360 -4 V6 C260 32 160 48 40 52 Z" fill="var(--brand-red-dark)" opacity="0.35"/>
  </svg>
</main>
</body>
</html>
```